Cocktail-Making Assistant App re-design

Ok boys and girls, here's the deal:
I have an android app which is almost complete, but needs a design overhaul.

The app is a standard cocktail-making assistant: gives you a list of cocktails and the ability to see which cocktail you can make out of those ingredients (drinks, fruit, etc) you have at home.

I've attached some general app flow, as well as detailed requirements/explanation presentation. Most of those things are just FYI, so that you know what it's about.

3 screens are the most important (main screen, cocktail view screen, ingredient view screen), meaning I will pick the design mostly based on ideas for those 3 things, with the fourth being a rather simple list (given on attached flow, third tier)
Some other screens are derived from that, with some minor changes on it, but you shouldn't care about that.

There are lots of other, non-explained things which I said nothing about only because they are (from design point of view) completely the same and would only make it seem more complicated.

I don't want to influence the colour scheme, but the app will be released under RedFig developer name (having a light colured red fig as a logo) so I suppose some brownish design, for example, will not really fit nicely. If you, however, have a killer which you are confident will prove me wrong, I'm looking forward to seeing it!

It should be a serious, elegant look (as opposed to cartoonish, but we are not aiming for a business look at all!), not cluttered with details, no clubbing themes, glitter and so on.

Test apk file available on request (Android 2.3+).

Edit: payment is now guaranteed
Also please note that currently, the favorite, "heart" button has a motion effect:
on click it flies out of the screen to the left (white heart) and comes back to the screen as a red heart. Take that into consideration, if it means anything to you.

Target Market(s)

Whoever you imagine would enjoy drinking cocktails

Industry/Entity Type

Business

Requirements
Must have
• Everything is said in the provided documentation - images say more than I could possibly write here.
Nice to have
• As said, most of the icons are a nice-to-have. Only those which are critically linked to the rest of the design must be provided. More details in the docs.
Should not have
• No cartoon look, No zillion colours

```html
<!DOCTYPE html>
<html lang="en">
<head>
<meta charset="utf-8">
<title>RedFig – cocktail search</title>
<link href="https://fonts.googleapis.com/css2?family=Open+Sans:wght@400;600&family=Roboto+Condensed:wght@400&display=swap" rel="stylesheet">
<style>
:root{
  --band:#575757;
  --ink:#000;
  --panel-line:#8a8a8a;
  --rule:#6b6b6b;
  --text:#ffffff;
  --accent:#e8275a;
  --title-warm:#f6d2a6;
  --field:#dcdcdc;
  --field-text:#8c8c8c;
  --blue:#2f86d6;
  --dot-blue:#3b9be8;
  --dot-green:#8cc63f;
  --dot-white:#e8e8e8;
  --star:#9a9a9a;
  --highlight:#cfcfcf;
  --sans:"Open Sans",Arial,sans-serif;
  --cond:"Roboto Condensed","Arial Narrow",sans-serif;
}
*{box-sizing:border-box;margin:0;padding:0}
html,body{width:1000px;height:1200px;overflow:hidden;background:var(--ink)}
body{position:relative;font-family:var(--sans);color:var(--text)}
.abs{position:absolute}
.top-band{left:0;top:0;width:1000px;height:146px;background:var(--band)}
.bottom-band{left:0;top:1131px;width:1000px;height:69px;background:var(--band)}
.brand{font-family:var(--sans);font-weight:400;color:var(--accent);letter-spacing:-1px}
.brand--large{left:66px;top:22px;font-size:72px;line-height:1}
.brand--small{left:0;width:1000px;top:1148px;font-size:30px;line-height:1;text-align:center}
.panel{border:1px solid var(--panel-line)}
.search-panel{left:20px;top:147px;width:508px;height:659px;border-top:none}
.detail-panel{left:573px;top:147px;width:402px;height:541px;border-top:none}
.desc-panel{left:598px;top:697px;width:371px;height:431px}
.home-icon{width:56px;height:56px}
.screen-title{font-size:48px;font-weight:400;line-height:1}
.rule{height:1px;background:var(--rule)}
.search-field{left:66px;top:233px;width:323px;height:44px;background:var(--field);color:var(--field-text);font-size:28px;line-height:44px;padding-left:14px}
.search-button{left:406px;top:233px;width:45px;height:43px}
.thumb{border-radius:3px}
.drink-name{font-size:30px;line-height:1;white-space:nowrap}
.drink-name small{font-size:22px}
.drink-name--selected{background:var(--highlight);color:#111;padding:2px 0 4px 2px}
.stars{height:28px}
.have-count{font-size:22px;color:var(--accent);white-space:nowrap}
.recipe-title{font-weight:400;color:var(--title-warm);white-space:nowrap;line-height:1}
.recipe-title--list{font-family:var(--sans);font-size:23px}
.recipe-title--desc{font-family:var(--cond);font-size:25px}
.camera{width:50px;height:42px}
.fav{font-size:25px;white-space:nowrap;line-height:1;display:flex;align-items:center;gap:10px}
.ingredient{left:660px;font-size:20px;line-height:1;white-space:nowrap}
.ingredient .brand-note{display:block;font-size:15px;margin:4px 0 0 18px}
.dot{width:15px;height:15px;border-radius:50%}
.tab-label{left:683px;top:672px;width:131px;height:38px;background:var(--field);color:#222;font-size:19px;text-align:center;line-height:38px}
.description{left:614px;top:864px;width:350px;font-family:var(--cond);font-size:21px;letter-spacing:-0.4px;line-height:38.5px;text-indent:40px}
.serve-in{left:648px;top:1072px;font-family:var(--cond);font-size:27px;white-space:nowrap}
</style>
</head>
<body>

<svg width="0" height="0" class="abs" aria-hidden="true">
  <defs>
    <symbol id="star" viewBox="0 0 24 24">
      <polygon points="12,1.5 14.9,8.6 22.5,9.2 16.7,14.2 18.5,21.6 12,17.6 5.5,21.6 7.3,14.2 1.5,9.2 9.1,8.6" fill="#1a1a1a" stroke="var(--star)" stroke-width="1.6"/>
    </symbol>
    <symbol id="star-row" viewBox="0 0 170 28">
      <use href="#star" x="0" y="0" width="28" height="28"/>
      <use href="#star" x="35" y="0" width="28" height="28"/>
      <use href="#star" x="70" y="0" width="28" height="28"/>
      <use href="#star" x="105" y="0" width="28" height="28"/>
      <use href="#star" x="140" y="0" width="28" height="28"/>
    </symbol>
    <symbol id="home" viewBox="0 0 56 56">
      <circle cx="28" cy="28" r="27" fill="#1e5fae"/>
      <circle cx="28" cy="28" r="22" fill="var(--blue)"/>
      <path d="M28 13 L43 27 H38 V41 H18 V27 H13 Z" fill="#fff"/>
      <rect x="24" y="31" width="8" height="10" fill="var(--blue)"/>
    </symbol>
    <symbol id="camera" viewBox="0 0 50 42">
      <rect x="1" y="1" width="48" height="40" rx="4" fill="#fff"/>
      <rect x="8" y="12" width="34" height="22" rx="3" fill="#111"/>
      <rect x="18" y="8" width="14" height="6" rx="2" fill="#111"/>
      <circle cx="25" cy="23" r="7" fill="#fff"/>
      <circle cx="25" cy="23" r="4" fill="#111"/>
    </symbol>
  </defs>
</svg>

<div class="abs top-band"></div>
<div class="abs brand brand--large">redfig</div>

<!-- Cocktail search screen -->
<section class="abs panel search-panel" aria-label="cocktail search"></section>
<svg class="abs home-icon" style="left:40px;top:157px" aria-hidden="true"><use href="#home"/></svg>
<h1 class="abs screen-title" style="left:126px;top:160px">cocktail search</h1>
<div class="abs rule" style="left:45px;top:221px;width:417px"></div>
<div class="abs search-field">search all</div>
<svg class="abs search-button" viewBox="0 0 45 43" aria-label="search">
  <rect width="45" height="43" rx="5" fill="var(--blue)"/>
  <circle cx="20" cy="19" r="9" fill="none" stroke="#fff" stroke-width="4"/>
  <line x1="27" y1="26" x2="35" y2="34" stroke="#fff" stroke-width="5" stroke-linecap="round"/>
</svg>

<ul class="drink-list" style="list-style:none">
  <li>
    <div class="abs thumb" role="img" aria-label="layered shot glass" style="left:46px;top:288px;width:24px;height:62px;background:linear-gradient(#e88a2a,#6b2a10 70%,#ddd)"></div>
    <div class="abs drink-name" style="left:100px;top:286px">’57 roadster</div>
    <svg class="abs stars" style="left:100px;top:324px;width:170px"><use href="#star-row"/></svg>
    <div class="abs have-count" style="left:318px;top:328px">Have &nbsp;0 of 4</div>
  </li>
  <li>
    <div class="abs thumb" role="img" aria-label="tall orange cocktail with fruit" style="left:40px;top:376px;width:34px;height:76px;background:linear-gradient(#f6c04a,#e88a18)"></div>
    <div class="abs drink-name" style="left:100px;top:376px">’57roadster <small>with a white</small></div>
    <div class="abs drink-name" style="left:104px;top:416px"><small>licence plate</small></div>
    <svg class="abs stars" style="left:108px;top:454px;width:170px"><use href="#star-row"/></svg>
    <div class="abs have-count" style="left:318px;top:456px">Have 0 of 2</div>
  </li>
  <li>
    <div class="abs thumb" role="img" aria-label="dark layered shot" style="left:42px;top:505px;width:38px;height:70px;background:linear-gradient(#c08b3a,#3a1a08)"></div>
    <div class="abs drink-name" style="left:104px;top:504px">1-900-MIX-ITUP</div>
    <svg class="abs stars" style="left:108px;top:544px;width:170px"><use href="#star-row"/></svg>
    <div class="abs have-count" style="left:318px;top:548px">Have 0 of 8</div>
  </li>
  <li>
    <div class="abs thumb" role="img" aria-label="creamy frozen cocktail glass" style="left:38px;top:605px;width:38px;height:64px;background:linear-gradient(#f4ecd6,#cbb48a)"></div>
    <div class="abs drink-name drink-name--selected" style="left:95px;top:611px;width:363px">151 Florida Bushwacker</div>
    <svg class="abs stars" style="left:108px;top:652px;width:170px"><use href="#star-row"/></svg>
    <div class="abs have-count" style="left:310px;top:656px">Have 0 of &nbsp;8</div>
  </li>
  <li>
    <div class="abs thumb" role="img" aria-label="red cocktail in martini glass" style="left:36px;top:716px;width:50px;height:46px;background:linear-gradient(#d2541c,#7a2008)"></div>
    <div class="abs drink-name" style="left:104px;top:720px">155 Fairmont</div>
    <svg class="abs stars" style="left:108px;top:760px;width:170px"><use href="#star-row"/></svg>
    <div class="abs have-count" style="left:318px;top:748px">Have 0 of 4</div>
  </li>
</ul>

<svg class="abs" style="left:468px;top:290px" width="32" height="472" viewBox="0 0 32 472" aria-label="scroll bar">
  <rect x="2" y="0" width="28" height="472" rx="4" fill="#f2f2f2" stroke="#bbb"/>
  <rect x="3" y="1" width="26" height="26" fill="#ddd"/>
  <polygon points="16,8 9,20 23,20" fill="#555"/>
  <rect x="3" y="445" width="26" height="26" fill="#ddd"/>
  <polygon points="16,464 9,452 23,452" fill="#555"/>
  <rect x="4" y="124" width="24" height="196" rx="12" fill="#7ec8f0" stroke="#3a9ad8" stroke-width="2"/>
  <rect x="8" y="130" width="8" height="184" rx="4" fill="#bfe6fb"/>
  <line x1="12" y1="215" x2="20" y2="215" stroke="#355" stroke-width="1.5"/>
  <line x1="12" y1="221" x2="20" y2="221" stroke="#355" stroke-width="1.5"/>
  <line x1="12" y1="227" x2="20" y2="227" stroke="#355" stroke-width="1.5"/>
</svg>

<svg class="abs" style="left:456px;top:408px" width="120" height="262" viewBox="0 0 120 262" aria-hidden="true">
  <polyline points="2,257 84,257 84,14 114,14" fill="none" stroke="#cfcfcf" stroke-width="1.5"/>
  <polyline points="106,2 117,14 106,26" fill="none" stroke="#cfcfcf" stroke-width="1.5"/>
</svg>

<!-- Cocktail view screen -->
<section class="abs panel detail-panel" aria-label="cocktail ingredients"></section>
<svg class="abs home-icon" style="left:579px;top:152px;width:44px;height:44px" aria-hidden="true"><use href="#home"/></svg>
<h2 class="abs recipe-title recipe-title--list" style="left:626px;top:165px">151 Florida bushwacker</h2>
<svg class="abs camera" style="left:910px;top:153px" aria-label="photo"><use href="#camera"/></svg>
<div class="abs rule" style="left:573px;top:208px;width:388px"></div>
<svg class="abs stars" style="left:600px;top:219px;width:160px;height:30px"><use href="#star-row"/></svg>
<div class="abs fav" style="left:600px;top:256px"><span style="font-size:22px">&#9829;</span>vol. unavailable</div>
<div class="abs thumb" role="img" aria-label="creamy frozen cocktail glass" style="left:884px;top:220px;width:38px;height:60px;background:linear-gradient(#f4ecd6,#cbb48a)"></div>
<div class="abs rule" style="left:598px;top:295px;width:332px;background:#aaa"></div>

<ul style="list-style:none">
  <li><span class="abs dot" style="left:613px;top:320px;background:var(--dot-blue)"></span><span class="abs ingredient" style="top:320px">1/2 &nbsp;oz Palmera rum</span></li>
  <li><span class="abs dot" style="left:613px;top:382px;background:var(--dot-blue)"></span><span class="abs ingredient" style="top:381px">1/2 oz Light rum</span></li>
  <li><span class="abs dot" style="left:613px;top:448px;background:var(--dot-green)"></span><span class="abs ingredient" style="top:444px">1/2 oz 151 proof rum<span class="brand-note">Caravel</span></span></li>
  <li><span class="abs dot" style="left:613px;top:508px;background:var(--dot-green)"></span><span class="abs ingredient" style="top:505px">1 oz Dark Creme de Cacao</span></li>
  <li><span class="abs dot" style="left:613px;top:569px;background:var(--dot-white)"></span><span class="abs ingredient" style="top:566px">1 oz Triple Sec</span></li>
  <li><span class="abs dot" style="left:613px;top:630px;background:var(--dot-white)"></span><span class="abs ingredient" style="top:627px">3 oz Milk</span></li>
</ul>
<div class="abs rule" style="left:632px;top:359px;width:290px"></div>
<div class="abs rule" style="left:632px;top:421px;width:290px"></div>
<div class="abs rule" style="left:626px;top:492px;width:290px"></div>
<div class="abs rule" style="left:632px;top:550px;width:284px"></div>
<div class="abs rule" style="left:632px;top:610px;width:288px"></div>

<!-- Description screen -->
<section class="abs panel desc-panel" aria-label="cocktail description"></section>
<div class="abs tab-label">Description</div>
<svg class="abs home-icon" style="left:604px;top:710px;width:46px;height:46px" aria-hidden="true"><use href="#home"/></svg>
<h2 class="abs recipe-title recipe-title--desc" style="left:655px;top:722px">151 Florida bushwacker</h2>
<svg class="abs camera" style="left:908px;top:708px" aria-label="photo"><use href="#camera"/></svg>
<div class="abs rule" style="left:636px;top:762px;width:290px"></div>
<svg class="abs stars" style="left:642px;top:778px;width:148px;height:28px"><use href="#star-row"/></svg>
<div class="abs fav" style="left:628px;top:822px"><span style="font-size:22px">&#9829;</span>vol. unavailable</div>
<div class="abs thumb" role="img" aria-label="creamy frozen cocktail glass" style="left:864px;top:780px;width:34px;height:58px;background:linear-gradient(#f4ecd6,#cbb48a)"></div>
<div class="abs rule" style="left:620px;top:851px;width:318px;background:#aaa"></div>
<p class="abs description">This frozen cocktail &nbsp;is full of sweet stuff including delicious dark rum, killer-coffee Cafetta and captivating &nbsp;coconut that mix with the creme de cacao for one of the best blended &nbsp;drinks out there.</p>
<div class="abs serve-in">Serve in : Beer mug</div>
<div class="abs thumb" role="img" aria-label="wooden beer mug" style="left:880px;top:1058px;width:40px;height:52px;background:linear-gradient(90deg,#c87a2a,#f0b050,#a85a18)"></div>

<div class="abs bottom-band"></div>
<div class="abs brand brand--small">redfig</div>

</body>
</html>
```